Business card for law firm

Need business card for new law firm. Think confident, authoritative, conservative, but not stuffy or old-fashioned.

Contact Information for Business Card

Content for card - logo (uploaded), plus the following:

Paul Whitcombe (larger font)
Managing Partner (larger font, but not as large as name)
Level 9, 7 Ferris Lane
Sydney NSW 2000
Main Tel 02 9364 2710
Direct Tel 02 8472 3159
Email paul@qvlegal.com.au
www.qvlegal.com.au

Letterhead design should include logo plus:
Level 9, 7 Ferris Lane
Sydney NSW 2000
Tel 02 8472 3159
www.qvlegal.com.au

```html
<!DOCTYPE html>
<html lang="en">
<head>
<meta charset="utf-8">
<title>Quayvale Lawyers – Business Card</title>
<link href="https://fonts.googleapis.com/css2?family=Open+Sans:wght@400;600;700&display=swap" rel="stylesheet">
<style>
  :root {
    --navy: #1b2a63;
    --ink: #1c1c1c;
    --text: #333333;
    --paper: #ffffff;
    --stage: #e9eaec;
    --rule: #d2d2d2;
    --swoosh-dark: #222222;
  }
  * { box-sizing: border-box; margin: 0; padding: 0; }
  html, body { width: 1200px; height: 900px; overflow: hidden; }
  body {
    background: var(--stage);
    font-family: "Open Sans", Arial, sans-serif;
    color: var(--text);
    position: relative;
  }
  .card {
    position: absolute;
    left: 250px;
    width: 700px;
    height: 400px;
    background: var(--paper);
    border-radius: 22px;
    overflow: hidden;
    box-shadow: 0 6px 18px rgba(0,0,0,0.12);
  }
  .card--front { top: 30px; }
  .card--back { top: 470px; }

  .swoosh { position: absolute; inset: 0; width: 100%; height: 100%; }

  .brand {
    position: absolute;
    display: flex;
    align-items: center;
    gap: 14px;
  }
  .brand__mark {
    width: 34px; height: 34px;
    background: var(--navy);
    flex: none;
  }
  .brand__name {
    font-weight: 400;
    color: var(--ink);
    letter-spacing: 0.08em;
    text-transform: uppercase;
    line-height: 1.15;
  }
  .card--front .brand { left: 60px; top: 160px; }
  .card--front .brand__name { font-size: 26px; }
  .card--back .brand { left: 50%; top: 50%; transform: translate(-50%, -50%); }
  .card--back .brand__mark { width: 44px; height: 44px; }
  .card--back .brand__name { font-size: 38px; }

  .divider {
    position: absolute;
    left: 400px; top: 70px;
    width: 1px; height: 210px;
    background: var(--rule);
  }

  .contact {
    position: absolute;
    left: 430px; top: 62px;
  }
  .contact__name {
    font-weight: 700;
    font-size: 22px;
    color: var(--navy);
    text-transform: uppercase;
    line-height: 1.1;
  }
  .contact__title { font-size: 16px; margin-bottom: 12px; }
  .contact__address { font-size: 15px; line-height: 1.35; margin-bottom: 12px; font-style: normal; }
  .contact__list { list-style: none; font-size: 15px; line-height: 1.45; }
  .contact__list li { display: flex; align-items: center; gap: 8px; }
  .contact__icon { width: 12px; height: 12px; fill: var(--navy); flex: none; }
</style>
</head>
<body>

  <section class="card card--front" aria-label="Business card front">
    <svg class="swoosh" viewBox="0 0 700 400" preserveAspectRatio="none" aria-hidden="true">
      <path d="M330 400 Q540 330 700 205 L700 400 Z" fill="var(--navy)"/>
      <path d="M0 400 L0 372 Q360 392 700 200 L700 222 Q400 400 0 400 Z" fill="var(--swoosh-dark)"/>
      <path d="M0 372 Q360 386 700 212 L700 222 Q380 398 0 384 Z" fill="var(--paper)" opacity="0.25"/>
    </svg>

    <div class="brand">
      <span class="brand__mark"></span>
      <span class="brand__name">Quayvale<br>Lawyers</span>
    </div>

    <div class="divider"></div>

    <div class="contact">
      <p class="contact__name">Paul Whitcombe</p>
      <p class="contact__title">Managing Partner</p>
      <address class="contact__address">Level 9, 7 Ferris Lane<br>Sydney NSW 2000</address>
      <ul class="contact__list">
        <li>
          <svg class="contact__icon" viewBox="0 0 24 24"><path d="M6.6 10.8a15.1 15.1 0 0 0 6.6 6.6l2.2-2.2a1 1 0 0 1 1-.25 11.4 11.4 0 0 0 3.6.57 1 1 0 0 1 1 1V20a1 1 0 0 1-1 1A17 17 0 0 1 3 4a1 1 0 0 1 1-1h3.5a1 1 0 0 1 1 1c0 1.25.2 2.46.57 3.6a1 1 0 0 1-.25 1z"/></svg>
          02 9364 2710 (Main)
        </li>
        <li>
          <svg class="contact__icon" viewBox="0 0 24 24"><path d="M6.6 10.8a15.1 15.1 0 0 0 6.6 6.6l2.2-2.2a1 1 0 0 1 1-.25 11.4 11.4 0 0 0 3.6.57 1 1 0 0 1 1 1V20a1 1 0 0 1-1 1A17 17 0 0 1 3 4a1 1 0 0 1 1-1h3.5a1 1 0 0 1 1 1c0 1.25.2 2.46.57 3.6a1 1 0 0 1-.25 1z"/></svg>
          02 8472 3159 (Direct)
        </li>
        <li>
          <svg class="contact__icon" viewBox="0 0 24 24"><path d="M2 5h20v14H2z M2 5l10 8 10-8" fill="none" stroke="var(--navy)" stroke-width="2.4"/></svg>
          paul@qvlegal.com.au
        </li>
        <li>
          <svg class="contact__icon" viewBox="0 0 24 24"><circle cx="12" cy="12" r="10" fill="none" stroke="var(--navy)" stroke-width="2.2"/><path d="M2 12h20M12 2c3 3 3 17 0 20M12 2c-3 3-3 17 0 20" fill="none" stroke="var(--navy)" stroke-width="1.8"/></svg>
          www.qvlegal.com.au
        </li>
      </ul>
    </div>
  </section>

  <section class="card card--back" aria-label="Business card back">
    <div class="brand">
      <span class="brand__mark"></span>
      <span class="brand__name">Quayvale<br>Lawyers</span>
    </div>
  </section>

</body>
</html>
```